Business Card for Coach - ready to print

Design Business Card ready to order prints www.lukasbrenner.coach

* An Overview / Background of the Business & Services
· Coaching
· Personal growth
* The Target Market / Audience you are trying to reach
· private person in different roles (self, familiy, business role)s
* Design Specifics; any preferences or ideas for Style, Colour, Imagery, etc
· See www.lukasbrenner.coach
· "simple" design
· (small) element of surprise / unusual element

* Information that will be placed in the Business Card
· Beratung und Coaching
· Address: Lukas Brenner, Mosering 42, CH-8312 Winterthur, Mobile +41 79 264 53 07
* Do you have an existing website or Facebook page where designers can learn more about your company?
· lukasbrenner.coach

Target Market(s)

private person in different roles (self, familiy, business role)

Industry/Entity Type

Life Coaching

Contact Information for Business Card

Lukas Brenner
Mosering 42
CH-8312 Winterthur

Mobile: +41 79 264 53 07
Email: lubr@alpimail.ch
www.lukasbrenner.coach

Font styles to use
Sans Serif

Colors

Designer to choose colors to be used in the design.

Requirements
Must have
• "simple" design
• element of surprise / unusual element
• Beratung & Coaching
• see www.lukasbrenner.coach for colors and so...
Nice to have
• TA Symbol (three rings on top of each other) - unsual presentation
• QR Code of Website (see if it fits in and still looks good).

```html
<!DOCTYPE html>
<html lang="de">
<head>
<meta charset="utf-8">
<title>Lukas Brenner – Visitenkarte</title>
<link href="https://fonts.googleapis.com/css2?family=Oswald:wght@500;600&family=Montserrat:wght@400&family=Roboto:wght@400&display=swap" rel="stylesheet">
<style>
  :root {
    --stage: #1c1e21;
    --card: #22272b;
    --card-edge: #2b3136;
    --silver: #9aa0a6;
    --ink-soft: #5d6469;
    --white: #f2f4f5;
    --text: #d9dde0;
    --accent: #4fc3f0;
    --photo-a: #c9cbcd;
    --photo-b: #8c9095;
  }
  * { box-sizing: border-box; margin: 0; padding: 0; }
  html, body { width: 1200px; height: 800px; overflow: hidden; background: var(--stage); }
  .canvas { position: relative; width: 1200px; height: 800px; }

  .card {
    position: absolute; top: 225px; width: 540px; height: 350px;
    background: var(--card); border-radius: 18px;
    box-shadow: 0 0 0 1px var(--card-edge), 0 18px 40px rgba(0,0,0,.45);
  }
  .card--front { left: 40px; }
  .card--back { left: 620px; }

  /* Front */
  .brand { position: absolute; left: 0; right: 0; top: 118px; text-align: center; }
  .brand__name {
    font-family: "Oswald", sans-serif; font-weight: 600; font-size: 78px;
    line-height: 1; letter-spacing: -1px; color: var(--silver); text-transform: uppercase;
  }
  .brand__tagline {
    margin-top: 8px; padding-left: 150px;
    font-family: "Montserrat", sans-serif; font-size: 17px; letter-spacing: 1.5px;
    color: var(--ink-soft);
  }

  /* Back */
  .portrait {
    position: absolute; left: 92px; top: 142px; width: 156px; height: 156px;
    border-radius: 50%; border: 5px solid var(--accent);
    background: radial-gradient(circle at 50% 40%, var(--photo-a), var(--photo-b));
  }
  .divider {
    position: absolute; left: 296px; top: 60px; width: 2px; height: 150px;
    background: linear-gradient(to bottom, transparent, var(--accent) 30%, var(--accent) 70%, transparent);
  }
  .contact { position: absolute; left: 322px; top: 62px; color: var(--text); font-family: "Roboto", sans-serif; }
  .contact__name {
    font-family: "Oswald", sans-serif; font-weight: 500; font-size: 30px; line-height: 1.1;
    color: var(--white); letter-spacing: -.3px; margin-bottom: 10px;
  }
  .contact__address { font-size: 14px; line-height: 1.4; margin-bottom: 10px; }
  .contact__list { list-style: none; font-size: 14px; line-height: 1.55; }
  .contact__item { display: flex; align-items: center; gap: 8px; }
  .contact__item svg { width: 13px; height: 13px; flex: none; }
  .contact__accent { color: var(--accent); }
</style>
</head>
<body>
<main class="canvas">

  <section class="card card--front" aria-label="Vorderseite">
    <div class="brand">
      <h1 class="brand__name">Lukas Brenner</h1>
      <p class="brand__tagline">Life Coaching</p>
    </div>
  </section>

  <section class="card card--back" aria-label="Rückseite">
    <div class="portrait" role="img" aria-label="Porträtfoto von Lukas Brenner"></div>
    <div class="divider"></div>
    <div class="contact">
      <h2 class="contact__name">LUKAS BRENNER</h2>
      <p class="contact__address">Mosering 42<br>CH-8312 Winterthur</p>
      <ul class="contact__list">
        <li class="contact__item">
          <svg viewBox="0 0 13 13" aria-hidden="true"><rect x="3" y="1" width="7" height="11" rx="1.2" fill="none" stroke="#4fc3f0" stroke-width="1.3"/><circle cx="6.5" cy="10" r=".7" fill="#4fc3f0"/></svg>
          +41 79 264 53 07
        </li>
        <li class="contact__item">
          <svg viewBox="0 0 13 13" aria-hidden="true"><rect x="1" y="3" width="11" height="8" fill="#4fc3f0"/><path d="M1 3l5.5 4.5L12 3" fill="none" stroke="#22272b" stroke-width="1.1"/></svg>
          lubr@alpimail.ch
        </li>
        <li class="contact__item">
          <svg viewBox="0 0 13 13" aria-hidden="true"><circle cx="6.5" cy="6.5" r="5.3" fill="none" stroke="#4fc3f0" stroke-width="1.2"/><ellipse cx="6.5" cy="6.5" rx="2.2" ry="5.3" fill="none" stroke="#4fc3f0" stroke-width="1"/><path d="M1.2 6.5h10.6" stroke="#4fc3f0" stroke-width="1"/></svg>
          <span>www.<span class="contact__accent">lukasbrenner</span>.coach</span>
        </li>
      </ul>
    </div>
  </section>

</main>
</body>
</html>
```